Brackwell Exteriors Needs a New Website!

We are an exteriors company specializing in vinyl siding, Corwin Maddox siding, aluminum soffit/fascia, trough. We do new construction work as well as renovations. We also build detached garages.
You can view our current website at www.brackwellfabricators.ca
I want to completely overhaul the website.
Our services are different now as we no longer do new home construction as well as we do not do the snow clearing.
I want to focus on 2 things in particular on the website:

1/ Exterior renovations

2/ Detached Garage construction.

I have included our logo in the attached files to use as well.

Some features we would like:

1/ Be able to easily attach a video from Clipverse/Reelio to highlight a product or service
2/ Quick chat or contact button that we can talk to a potential client quickly
3/ Meet the Team page that is interesting and fresh
4/ Place for us to put in helpful exterior tips/suggestions for homeowners.

Content is not important, but looking for the best design that will attract people once they click on our page and want to renovate with us.

Target Market(s)

People looking for renovations on their home, people looking to build a detached garage.

Industry/Entity Type

Residential Construction

Number of Pages Required

5+ page

Font styles to use
Sans Serif

Requirements
Must have
• Fresh and exciting home page.

Simple design. Don't want it over complicated or too much information to confuse the potential client.

Easy way to contact us.

Meet the team page that instills confidence
Nice to have
• Colour of website to go off our logo. Doesn't need to be an exact match, but something that goes well with our blue and grey.

```html
<!DOCTYPE html>
<html lang="en">
<head>
<meta charset="utf-8">
<title>About Us – Brackwell Exteriors</title>
<link rel="stylesheet" href="https://fonts.googleapis.com/css2?family=Montserrat:wght@400;500;600;700;800&display=swap">
<style>
:root{
  --blue:#0a6fc2;
  --blue-deep:#0663b0;
  --blue-light:#1a82d1;
  --ink:#111418;
  --text:#3a3f45;
  --page:#f5f9fc;
  --card:#dfeff9;
  --field-border:#c9d3dc;
  --hero-top:#c7ccd2;
  --hero-mid:#8f8c8b;
  --hero-low:#5b5a5d;
  --bar:#0b0b0c;
  --white:#ffffff;
}
*{box-sizing:border-box;margin:0;padding:0}
html,body{width:1200px;height:2618px;overflow:hidden}
body{position:relative;background:var(--page);font-family:'Montserrat',sans-serif;color:var(--text)}
.abs{position:absolute}

/* hero */
.hero{left:0;top:0;width:1200px;height:600px}
.site-header{left:0;top:0;width:1200px;height:92px}
.brand{left:162px;top:26px;display:flex;align-items:center;gap:10px;color:var(--blue);font-weight:700;font-size:25px;letter-spacing:.5px}
.brand-dot{width:36px;height:36px;border:3px solid var(--blue);border-radius:50%}
.main-nav{top:38px;font-size:13px;font-weight:500;color:var(--ink);letter-spacing:.2px}
.main-nav span{position:absolute;white-space:nowrap;transform:translateX(-50%)}
.main-nav .active{color:var(--blue);font-weight:700}
.nav-underline{left:579px;top:88px;width:75px;height:3px;background:var(--blue)}
.header-rule{left:162px;top:91px;width:876px;height:1px;background:rgba(255,255,255,.45)}
.hero-title{left:162px;top:268px;font-size:43px;font-weight:800;color:var(--white);letter-spacing:.5px}
.crumbs{left:163px;top:326px;font-size:12px;color:var(--white);font-weight:500}

/* section headings */
.section-title{left:0;width:1200px;text-align:center;font-size:29px;font-weight:800;color:var(--ink);letter-spacing:.6px}
.section-title b{color:var(--blue);font-weight:800}
.title-rule{left:570px;width:60px;height:2px;background:var(--blue)}

.photo{border-radius:16px}
.photo-site{left:163px;top:683px;width:396px;height:359px;background:linear-gradient(180deg,#a7a9ab 0%,#8a8b8c 45%,#5f5750 70%,#4a4037 100%)}
.photo-kitchen{left:641px;top:1119px;width:396px;height:359px;background:linear-gradient(180deg,#d9dadc 0%,#9b9089 45%,#7a716b 65%,#b9b4ad 100%)}

.copy{font-size:12.6px;line-height:23px;text-align:justify;color:var(--text)}
.copy .lead{font-size:14.5px;line-height:24px;color:#222;margin-bottom:6px}
.copy p{margin-bottom:6px}
.copy-one{left:602px;top:683px;width:436px}
.copy-two{left:161px;top:1120px;width:437px}
.divider{left:161px;top:1080px;width:877px;border-top:1px dashed #c9cfd5}

/* inquiry */
.card-shadow-2{left:174px;top:2050px;width:850px;height:47px;background:#5b9fd8;border-radius:0 0 10px 10px}
.card-shadow-1{left:166px;top:2040px;width:864px;height:44px;background:#b6d7ef;border-radius:0 0 10px 10px}
.inquiry{left:160px;top:1562px;width:877px;height:506px;background:var(--card);border-radius:10px}
.field{background:var(--white);border:1px solid var(--field-border);border-radius:3px;font-size:11.5px;color:#6b727a;padding:14px 16px}
.f-name{left:205px;top:1687px;width:383px;height:42px}
.f-phone{left:609px;top:1687px;width:383px;height:42px}
.f-email{left:205px;top:1743px;width:383px;height:42px}
.f-service{left:609px;top:1743px;width:383px;height:42px}
.f-message{left:205px;top:1798px;width:787px;height:97px}
.chev{position:absolute;right:16px;top:18px}
.captcha{left:466px;top:1907px;width:265px;height:44px;background:#f9f9f9;border:1px solid #d3d3d3;border-radius:3px;font-size:10px;color:#222}
.captcha .box{position:absolute;left:10px;top:12px;width:20px;height:20px;border:2px solid #c1c1c1;border-radius:2px;background:#fff}
.captcha .label{position:absolute;left:37px;top:15px}
.captcha .mark{position:absolute;right:12px;top:7px;width:18px;height:18px;border-radius:50%;background:#4a90e2}
.captcha .tiny{position:absolute;right:6px;top:29px;font-size:5px;color:#777}
.submit{left:539px;top:1967px;width:122px;height:37px;background:var(--blue);color:#fff;font-size:12px;font-weight:700;letter-spacing:.6px;text-align:center;line-height:37px;border-radius:2px}
.chat{left:1113px;top:1758px;width:63px;height:63px;border-radius:50%;background:#fff;box-shadow:0 3px 12px rgba(0,0,0,.12)}

/* footer */
.footer-bg{left:0;top:1790px;width:1200px;height:772px}
.foot-brand{left:0;width:1200px;top:2206px;display:flex;justify-content:center;align-items:center;gap:14px;color:#fff;font-weight:700;font-size:40px;letter-spacing:.5px}
.foot-brand .brand-dot{width:72px;height:72px;border:5px solid #fff}
.foot-nav{top:2325px;font-size:14.5px;font-weight:500;color:#fff}
.foot-nav span{position:absolute;white-space:nowrap;transform:translateX(-50%)}
.foot-sep{top:2327px;width:1px;height:14px;background:rgba(255,255,255,.35)}
.contact{top:2400px;width:300px;text-align:center;color:#fff}
.contact svg{display:block;margin:0 auto 12px}
.contact h4{font-size:14.5px;font-weight:700;letter-spacing:.4px;margin-bottom:5px}
.contact p{font-size:12.3px;line-height:20px}
.bottom-bar{left:0;top:2562px;width:1200px;height:56px;background:var(--bar)}
.copyright{left:161px;top:2582px;font-size:12.5px;color:#e8e8e8}
.social{top:2575px;width:30px;height:30px;border-radius:50%;background:var(--blue);border:2px solid #fff}
</style>
</head>
<body>

<svg class="abs hero" width="1200" height="600" viewBox="0 0 1200 600" role="img" aria-label="Photo of a finished kitchen with grey cabinets, granite island and tiled backsplash">
  <defs>
    <linearGradient id="heroFill" x1="0" y1="0" x2="0" y2="1">
      <stop offset="0" stop-color="#cfd4da"/>
      <stop offset=".3" stop-color="#9a9897"/>
      <stop offset=".65" stop-color="#6a6868"/>
      <stop offset="1" stop-color="#3f3f44"/>
    </linearGradient>
    <linearGradient id="heroTop" x1="0" y1="0" x2="0" y2="1">
      <stop offset="0" stop-color="#eef3f8" stop-opacity=".85"/>
      <stop offset="1" stop-color="#eef3f8" stop-opacity="0"/>
    </linearGradient>
  </defs>
  <polygon points="0,0 1200,0 1200,391 0,600" fill="url(#heroFill)"/>
  <polygon points="0,0 1200,0 1200,130 0,130" fill="url(#heroTop)"/>
</svg>

<header class="abs site-header">
  <div class="abs brand"><span class="brand-dot"></span>BRACKWELL</div>
  <nav class="abs main-nav" style="left:0;width:1200px">
    <span style="left:517px">HOME</span>
    <span class="active" style="left:616px">ABOUT US</span>
    <span style="left:723px">SERVICES</span>
    <span style="left:851px">MEET THE TEAM</span>
    <span style="left:997px">CONTACT US</span>
  </nav>
  <div class="abs header-rule"></div>
  <div class="abs nav-underline"></div>
</header>

<h1 class="abs hero-title">ABOUT US</h1>
<div class="abs crumbs">HOME - ABOUT US</div>

<h2 class="abs section-title" style="top:607px">ABOUT <b>US</b></h2>
<div class="abs title-rule" style="top:650px"></div>

<div class="abs photo photo-site" role="img" aria-label="Photo of a house under construction with wrapped walls and a new roof"></div>
<div class="abs copy copy-one">
  <p class="lead">We Are A People Looking For Renovations On Their Home, People Looking To Build A Detached Garage</p>
  <p>Lorem ipsum dolor sit amet, consectetuer adipiscing elit, sed diam nonummy nibh euismod tincidunt ut laoreet dolore magna aliquam erat volutpat. Ut wisi enim ad minim veniam, quis nostrud exerci tation ullamcorper suscipit lobortis nisl ut aliquip ex ea commodo consequat. Duis autem vel eum iriure dolor in hendrerit in vulputate velit esse molestie consequat, praesent luptatum zzril delenit augue duis dolore te feugait nulla facilisi.</p>
  <p>Sed ut perspiciatis unde omnis iste natus error sit voluptatem accusantium doloremque laudantium, totam rem aperiam, eaque ipsa quae ab illo inventore veritatis et quasi architecto beatae vitae dicta sunt explicabo. Nemo enim ipsam voluptatem quia voluptas sit aspernatur aut odit aut fugit, sed quia consequuntur magni dolores eos qui ratione voluptatem sequi nesciunt.</p>
</div>

<div class="abs divider"></div>

<div class="abs copy copy-two">
  <p class="lead">Ut enim ad minima veniam, quis nostrum exercitationem ullam corporis suscipit laboriosam, nisi ut commodi consequatur</p>
  <p>Lorem ipsum dolor sit amet, consectetuer adipiscing elit, sed diam nonummy nibh euismod tincidunt ut laoreet dolore magna aliquam erat volutpat. Ut wisi enim ad minim veniam, quis nostrud exerci tation ullamcorper suscipit lobortis nisl ut aliquip ex ea commodo consequat. Duis autem vel eum iriure dolor in hendrerit in vulputate velit esse molestie consequat, et accumsan et iusto odio dignissim qui blandit praesent luptatum zzril delenit augue duis dolore te feugait nulla facilisi.</p>
  <p>Sed ut perspiciatis unde omnis iste natus error sit voluptatem accusantium doloremque laudantium, totam rem aperiam, eaque ipsa quae ab illo inventore veritatis et quasi architecto beatae vitae dicta sunt explicabo. Nemo enim ipsam voluptatem quia voluptas sit aspernatur aut odit aut fugit, sed quia consequuntur magni dolores eos qui ratione voluptatem sequi nesciunt.</p>
</div>
<div class="abs photo photo-kitchen" role="img" aria-label="Photo of a bright kitchen with grey cabinets, island and track lighting"></div>

<svg class="abs footer-bg" width="1200" height="772" viewBox="0 0 1200 772" aria-hidden="true">
  <polygon points="0,196 1200,8 1200,772 0,772" fill="var(--blue)"/>
  <polygon points="0,340 1200,150 1200,330 0,510" fill="#0b74c6"/>
  <polygon points="0,560 1200,400 1200,520 0,700" fill="#0d78ca"/>
</svg>

<div class="abs card-shadow-2"></div>
<div class="abs card-shadow-1"></div>
<section class="abs inquiry"></section>
<h2 class="abs section-title" style="top:1616px">QUICK <b>INQUIRY</b></h2>
<div class="abs title-rule" style="top:1656px"></div>

<div class="abs field f-name">Name*</div>
<div class="abs field f-phone">Phone*</div>
<div class="abs field f-email">Email*</div>
<div class="abs field f-service">Choose a Service
  <svg class="chev" width="10" height="6" viewBox="0 0 10 6"><path d="M1 1l4 4 4-4" fill="none" stroke="#444" stroke-width="1.3"/></svg>
</div>
<div class="abs field f-message">Message*</div>
<div class="abs captcha">
  <span class="box"></span><span class="label">I'm not a robot</span>
  <span class="mark"></span><span class="tiny">Verified · Safe</span>
</div>
<div class="abs submit">SUBMIT</div>

<div class="abs chat">
  <svg width="63" height="63" viewBox="0 0 63 63" aria-label="Quick chat">
    <circle cx="28" cy="29" r="11" fill="none" stroke="var(--blue)" stroke-width="1.8"/>
    <path d="M36 24a10 10 0 0 1 3 17l2 5-6-3a10 10 0 0 1-9-2" fill="none" stroke="var(--blue)" stroke-width="1.8"/>
    <path d="M25 26a3 3 0 1 1 4 3v2" fill="none" stroke="var(--blue)" stroke-width="1.6"/>
    <circle cx="29" cy="34" r="1" fill="var(--blue)"/>
  </svg>
</div>

<div class="abs foot-brand"><span class="brand-dot"></span>BRACKWELL</div>
<nav class="abs foot-nav" style="left:0;width:1200px">
  <span style="left:311px">HOME</span>
  <span style="left:425px">ABOUT US</span>
  <span style="left:553px">SERVICES</span>
  <span style="left:703px">MEET THE TEAM</span>
  <span style="left:864px">CONTACT US</span>
</nav>
<div class="abs foot-sep" style="left:361px"></div>
<div class="abs foot-sep" style="left:491px"></div>
<div class="abs foot-sep" style="left:616px"></div>
<div class="abs foot-sep" style="left:790px"></div>

<div class="abs contact" style="left:107px">
  <svg width="28" height="46" viewBox="0 0 28 46"><rect x="2" y="2" width="24" height="42" rx="3" fill="none" stroke="#fff" stroke-width="1.6"/><line x1="2" y1="9" x2="26" y2="9" stroke="#fff" stroke-width="1.4"/><line x1="2" y1="36" x2="26" y2="36" stroke="#fff" stroke-width="1.4"/><circle cx="14" cy="40" r="1.6" fill="#fff"/></svg>
  <h4>PHONE</h4>
  <p>+1 780-555-0174</p>
</div>
<div class="abs contact" style="left:444px">
  <svg width="34" height="46" viewBox="0 0 34 46"><path d="M17 44C7 30 2 22 2 16a15 15 0 0 1 30 0c0 6-5 14-15 28z" fill="none" stroke="#fff" stroke-width="1.6"/><circle cx="17" cy="16" r="5" fill="none" stroke="#fff" stroke-width="1.6"/></svg>
  <h4>BRACKWELL EXTERIORS</h4>
  <p>4820 Alder Ridge Rd #118, Fenwick<br>Park, AB T9X 2L4, Canada</p>
</div>
<div class="abs contact" style="left:775px">
  <svg width="50" height="46" viewBox="0 0 50 46"><rect x="2" y="6" width="46" height="36" fill="none" stroke="#fff" stroke-width="1.6"/><path d="M2 6l23 20L48 6M2 42l17-16M48 42L31 26" fill="none" stroke="#fff" stroke-width="1.6"/></svg>
  <h4>EMAIL</h4>
  <p>hello@brackwellexteriors.ca</p>
</div>

<footer class="abs bottom-bar"></footer>
<div class="abs copyright">Copyright © 2020 &nbsp;BRACKWELL EXTERIORS. All Rights Reserved.</div>
<span class="abs social" style="left:890px" aria-label="Social link"></span>
<span class="abs social" style="left:929px" aria-label="Social link"></span>
<span class="abs social" style="left:967px" aria-label="Social link"></span>
<span class="abs social" style="left:1007px" aria-label="Social link"></span>

</body>
</html>
```